Business Cards for IT Consulting Company (Managed Service Provider)

I am looking to have some business cards printed and would like some designs. We are an IT Consulting company based in Vancouver BC. I would like a nice clean and modern look to the cards. I have uploaded all the versions of my logo so parts can be used as needed. Here is a snippit from our website homepage:

Quillbrook Networks Ltd. is an IT Solutions Partner located in Vancouver BC, Canada. We offer IT solutions and support to customers in the greater Vancouver Area. With expertise in Microsoft platforms, as well as Linux and Mac OSX and over 12 years experience in the IT industry, Quillbrook Networks is dedicated to offering our clients top quality service and products. We take pride in the solutions we offer our customers. The greatest compliment a client can give us is to recommend our services.

Quillbrook Networks Ltd. offers a wide range of IT services from onsite service to remote support and managed service solutions. This allows clients to choose the support path that best suits their company’s needs. Supporting many different sized companies from small to enterprise level over the past 12 years Quillbrook Networks has the experience and expertise needed to ensure things run smoothly. Allowing our clients to focus on doing business.

Revolutionizing the way IT services are delivered.

Quillbrook Networks is dedicated to providing our clients with IT solutions that work and grow with them for years to come. This philosophy helps save money in the long run instead of replacing equipment constantly. Far too often IT solutions are not well thought out and while possibly solving the problem at hand, require replacement due to growth or quality within a very short time frame. Quillbrook Networks takes pride in providing solutions that will last and be able to accommodate growth without the need for replacement.

Industry/Entity Type

Information Technology

Contact Information for Business Card

Quillbrook Networks Ltd.
(Employee Name)
Eml: (Employees Email Address)
Web: quillbrook.me
Ph: 604-555-0148

Font styles to use
Serif
Sans Serif

Requirements
Must have
• The Company logo and company colors.
Nice to have
• - Our tag line: "Revolutionizing IT Services" or "Revolutionizing the way IT services are delivered."
• - Also I really like the idea of nature and technology together blending which is sort of where my logo came from so integrating that somehow onto the business cards would be great.

```html
<!DOCTYPE html>
<html lang="en">
<head>
<meta charset="utf-8">
<title>Quillbrook Networks Ltd. – Business Cards</title>
<link href="https://fonts.googleapis.com/css2?family=Roboto:ital,wght@0,400;0,500;0,700;1,400&display=swap" rel="stylesheet">
<style>
  :root {
    --backdrop: #a9a7a8;
    --card: #f4f4f4;
    --brand-blue: #1a8bd0;
    --ink: #4a4a4c;
    --ink-dark: #3f3e40;
    --band-grey: #4b4a4c;
    --white: #ffffff;
  }
  * { box-sizing: border-box; margin: 0; padding: 0; }
  html, body {
    width: 1200px; height: 1200px; overflow: hidden;
    background: var(--backdrop);
    font-family: "Roboto", Arial, sans-serif;
  }
  .canvas { position: relative; width: 1200px; height: 1200px; }

  .card {
    position: absolute;
    width: 712px; height: 418px;
    background: var(--card);
    overflow: hidden;
  }
  .card--front { left: 238px; top: 118px; }
  .card--back  { left: 230px; top: 644px; }

  /* wordmark */
  .wordmark { position: absolute; display: flex; align-items: center; gap: 18px; }
  .wordmark__square { background: var(--brand-blue); flex: none; }
  .wordmark__text { color: var(--brand-blue); font-weight: 500; line-height: 1; }
  .wordmark__name { display: block; letter-spacing: -0.5px; }
  .wordmark__sub { display: block; letter-spacing: 1px; margin-top: 6px; }

  .card--front .wordmark { left: 110px; top: 142px; }
  .card--front .wordmark__square { width: 70px; height: 70px; }
  .card--front .wordmark__name { font-size: 74px; }
  .card--front .wordmark__sub { font-size: 25px; }

  .card--back .wordmark { right: 56px; top: 172px; flex-direction: column; align-items: flex-start; gap: 0; }
  .card--back .wordmark__name { font-size: 46px; }
  .card--back .wordmark__sub { font-size: 17px; margin-top: 4px; }

  /* tagline on front */
  .tagline-rule {
    position: absolute; left: 0; right: 0; top: 376px;
    display: flex; align-items: center; justify-content: center; gap: 16px;
  }
  .tagline-rule__line { width: 110px; height: 3px; background: var(--brand-blue); }
  .tagline-rule__text { font-size: 19px; color: var(--ink); letter-spacing: 0.3px; }

  /* person */
  .person { position: absolute; left: 41px; top: 66px; }
  .person__name { font-size: 25px; font-weight: 700; color: var(--brand-blue); }
  .person__title { font-size: 16px; font-style: italic; color: var(--ink); margin-top: 6px; }

  /* contact */
  .contact { position: absolute; left: 41px; top: 244px; list-style: none; }
  .contact__item {
    display: flex; align-items: center; gap: 17px;
    font-size: 18px; color: var(--ink-dark); height: 27.5px;
  }
  .contact__icon { width: 18px; height: 18px; flex: none; }

  .band { position: absolute; left: 0; bottom: 0; width: 712px; height: 120px; }
  .band__tagline {
    position: absolute; right: 50px; bottom: 23px;
    font-size: 18.5px; color: var(--white); letter-spacing: 0.3px;
  }
</style>
</head>
<body>
<main class="canvas">

  <section class="card card--front" aria-label="Card front">
    <div class="wordmark">
      <span class="wordmark__square"></span>
      <span class="wordmark__text">
        <span class="wordmark__name">quillbrook</span>
        <span class="wordmark__sub">NETWORKS LTD.</span>
      </span>
    </div>
    <div class="tagline-rule">
      <span class="tagline-rule__line"></span>
      <span class="tagline-rule__text">Revolutionizing IT Services</span>
      <span class="tagline-rule__line"></span>
    </div>
  </section>

  <section class="card card--back" aria-label="Card back">
    <div class="person">
      <p class="person__name">Daniel Harper</p>
      <p class="person__title">Managing Director</p>
    </div>

    <div class="wordmark">
      <span class="wordmark__text">
        <span class="wordmark__name">quillbrook</span>
        <span class="wordmark__sub">NETWORKS LTD.</span>
      </span>
    </div>

    <ul class="contact">
      <li class="contact__item">
        <svg class="contact__icon" viewBox="0 0 18 18" aria-hidden="true">
          <path d="M2 6 Q9 1 16 6 L14 8 L12 6.5 L6 6.5 L4 8 Z" fill="var(--brand-blue)"/>
          <rect x="3" y="9" width="12" height="7" rx="1" fill="var(--brand-blue)"/>
          <circle cx="9" cy="12.5" r="1.8" fill="var(--card)"/>
        </svg>
        604-555-0148
      </li>
      <li class="contact__item">
        <svg class="contact__icon" viewBox="0 0 18 18" aria-hidden="true" fill="none" stroke="var(--brand-blue)" stroke-width="1.6">
          <circle cx="9" cy="9" r="7"/>
          <ellipse cx="9" cy="9" rx="3" ry="7"/>
          <line x1="2" y1="9" x2="16" y2="9"/>
        </svg>
        www.quillbrook.me
      </li>
      <li class="contact__item">
        <svg class="contact__icon" viewBox="0 0 18 18" aria-hidden="true">
          <rect x="1" y="4" width="16" height="11" fill="var(--brand-blue)"/>
          <path d="M1 4 L9 10.5 L17 4" fill="none" stroke="var(--card)" stroke-width="1.4"/>
        </svg>
        support@quillbrook.me
      </li>
    </ul>

    <svg class="band" viewBox="0 0 712 120" preserveAspectRatio="none" aria-hidden="true">
      <path d="M112 120 Q380 25 712 22 L712 120 Z" fill="var(--band-grey)"/>
      <path d="M150 120 Q400 38 712 34 L712 120 Z" fill="var(--brand-blue)"/>
    </svg>
    <p class="band__tagline">Revolutionizing IT Services</p>
  </section>

</main>
</body>
</html>
```